Build Website for Playful Brand that helps content creators build businesses

Please help me create a website for my company that helps content creators build businesses around their audience. I have attached a design and vibe that I am going for at mossquay.io.

Open for changes, but I want to keep the colour I currently have (a light teal). Ultimately the brand is playful but should come off as a very modern elevated brand.

I am looking for a few pages including

1. Home (with clear CTA button)
A section where I can input what the company does, and some brands that we have launched

2. About Me
A simple page, that has preferably able to put a circular image of myself and then give a quick background about the company

3. Blog (can you include how blog posts will appear and it should sit nicely in the page)
This ideally is a section that will be able to link to another software so my blogs automatically flow into here or posts. But otherwise it should have sections of blocks where creators can see about topics that I post about

4. Contact (this should include a form that will allow users to contact me)
Finally a contact page where it links my socials, similar what is there, but ideally there is a form they can fill out which I can link to my inbox as well. This should be a simple page as well

Create a multi page website, including a page that will link or can link blog post

Similar to this vibe and logo - https://mossquay.io/

Target Market(s)

Content Creators

Coding

Coded - Design and coding required

Number of Pages Required

4 page

Requirements
Must have
• Home, Contact Me (Including a place to submit an enquiry and form), Blog Post Page As well

```html
<!DOCTYPE html>
<html lang="en">
<head>
<meta charset="UTF-8">
<title>Moss Quay — Building Businesses</title>
<link href="https://fonts.googleapis.com/css2?family=Montserrat:wght@400;500;600;700&family=Open+Sans:wght@400;600&display=swap" rel="stylesheet">
<style>
:root{
  --slate:#445a63;
  --slate-dark:#34474f;
  --ink:#1d2529;
  --muted:#6f7a80;
  --teal-light:#e3f2f7;
  --tint:#f2f8fb;
  --white:#ffffff;
  --black:#060606;
}
*{box-sizing:border-box;margin:0;padding:0}
html,body{width:1200px;height:4310px;overflow:hidden}
body{font-family:"Open Sans",Arial,sans-serif;color:var(--ink);background:var(--white);position:relative}
.head{font-family:"Montserrat",Arial,sans-serif}
section,header,footer{position:relative;width:1200px}
.abs{position:absolute}
.btn{position:absolute;background:var(--slate);color:var(--white);font-family:"Montserrat",Arial,sans-serif;font-weight:600;display:flex;align-items:center;justify-content:center;box-shadow:0 3px 6px rgba(0,0,0,.2);border-radius:2px}
.title{font-family:"Montserrat",Arial,sans-serif;font-size:32px;color:var(--slate);font-weight:400;letter-spacing:.5px}
.title b{font-weight:700}
.rule{height:4px;width:54px;background:var(--slate)}

/* header */
.site-header{height:95px}
.brand{left:98px;top:6px;width:125px;text-align:center}
.brand-mark{width:52px;height:52px;border-radius:50%;background:var(--teal-light);margin:0 auto 4px}
.brand-name{font-family:"Montserrat",Arial,sans-serif;font-size:15px;letter-spacing:2px;color:var(--slate)}
.nav{left:664px;top:34px;display:flex;gap:38px;font-family:"Montserrat",Arial,sans-serif;font-size:15px;color:var(--ink)}
.nav .active{text-decoration:underline;text-underline-offset:4px}
.search{left:918px;top:33px}
.nav-cta{left:965px;top:22px;width:137px;height:46px;font-size:14px;font-weight:500}

/* hero */
.hero{height:557px;background:linear-gradient(100deg,#f5f9fb 0%,#eef5f8 100%)}
.hero-kicker{left:97px;top:142px;font-size:32px;font-weight:600}
.hero-kicker span{font-weight:400}
.hero-title{left:95px;top:188px;font-size:49px;color:var(--slate);font-weight:400}
.hero-title b{font-weight:700}
.hero-rule{left:97px;top:260px;width:76px;height:3px}
.hero-sub{left:96px;top:282px;font-size:18px}
.hero-cta{left:97px;top:330px;width:138px;height:47px;font-size:15px}
.hero-art{left:620px;top:50px;width:450px;height:460px;border-radius:24px;background:linear-gradient(160deg,#dcebf1 0%,#eef2f4 55%,#f6dcb4 100%)}

/* about */
.about{height:588px}
.about-art{left:108px;top:58px;width:464px;height:464px;border-radius:50%;background:radial-gradient(circle at 50% 45%,#7d9199 0%,#53666e 60%,#4a5d65 100%);box-shadow:0 0 0 14px #e8f4f8}
.about-head{left:643px;top:78px}
.about-rule{left:643px;top:115px}
.about-lead{left:643px;top:146px;width:420px;font-size:15px;font-weight:600;line-height:28px}
.about-text{left:643px;top:213px;width:450px;font-size:14px;line-height:28.5px;color:var(--muted)}
.about-btn{left:643px;top:428px;width:136px;height:47px;font-size:15px}

/* how it works */
.how{height:645px;background:var(--slate)}
.how .title{color:var(--white)}
.how-head{left:0;width:1200px;top:75px;text-align:center}
.how-rule{left:573px;top:130px;background:var(--white)}
.how-text{left:120px;top:150px;width:960px;text-align:center;color:var(--white);font-size:15px;line-height:30px}
.step{position:absolute;top:238px;height:264px;background:var(--teal-light);border-radius:4px;text-align:center;padding-top:23px}
.step.featured{background:var(--slate);border:2px solid var(--white);border-radius:6px;height:300px;top:236px;color:var(--white)}
.step-icon{width:110px;height:110px;border-radius:50%;background:var(--slate);margin:0 auto 22px;display:flex;align-items:center;justify-content:center}
.featured .step-icon{background:var(--white)}
.step h3{font-family:"Montserrat",Arial,sans-serif;font-size:18px;font-weight:500;margin-bottom:6px}
.step p{font-size:14.5px;line-height:30px;padding:0 26px}

/* why */
.why{height:633px}
.why-head{left:0;width:1200px;top:75px;text-align:center}
.why-rule{left:573px;top:128px}
.why-text{left:0;width:1200px;top:148px;text-align:center;font-size:15px}
.reason{position:absolute;width:490px;height:95px;background:var(--tint);display:flex}
.reason-icon{width:110px;height:95px;background:var(--slate);display:flex;align-items:center;justify-content:center;flex:none}
.reason-body{padding:17px 20px 0 20px}
.reason h4{font-family:"Montserrat",Arial,sans-serif;font-size:15.5px;font-weight:500;margin-bottom:4px}
.reason p{font-size:14px;line-height:25px;color:#3b4448}

/* blog */
.blog{height:695px;background:var(--tint)}
.blog-head{left:0;width:1200px;top:63px;text-align:center}
.blog-rule{left:573px;top:118px}
.post{position:absolute;top:165px;width:306px;height:444px;background:var(--white);box-shadow:0 4px 14px rgba(0,0,0,.12)}
.post-photo{height:173px}
.post h3{font-family:"Open Sans",Arial,sans-serif;font-weight:400;font-size:21px;line-height:33px;margin:22px 30px 14px}
.post p{font-size:17px;line-height:33px;margin:0 30px}
.post .more{position:absolute;left:30px;bottom:30px;font-family:"Montserrat",Arial,sans-serif;font-weight:500;font-size:16px;display:flex;align-items:center;gap:12px}

/* contact */
.contact{height:512px}
.contact-head{left:0;width:1200px;top:65px;text-align:center}
.field{position:absolute;background:var(--white);border:1px solid #eef0f1;box-shadow:0 4px 10px rgba(0,0,0,.08);font-size:13px;color:var(--muted);padding:14px 16px}
.submit{left:531px;top:377px;width:136px;height:50px;font-size:16px}

/* footer */
.site-footer{height:585px;background:var(--black);color:var(--white)}
.partner{position:absolute;top:50px;display:flex;align-items:center;gap:14px}
.partner-mark{width:78px;height:78px;border-radius:50%;background:#2a2a2a}
.partner-bar{width:95px;height:22px;background:#2a2a2a;border-radius:3px}
.foot-rule{left:110px;top:200px;width:980px;height:1px;background:#3a3a3a}
.foot-brand{left:140px;top:215px;width:200px;text-align:center}
.foot-mark{width:88px;height:88px;border-radius:50%;background:#bfe3ec;margin:0 auto 12px}
.foot-name{font-family:"Open Sans",Arial,sans-serif;font-size:23px;line-height:30px;letter-spacing:4px;color:#5f8fa0}
.foot-contact{left:137px;top:368px;font-size:17px;line-height:34px}
.social{left:197px;top:448px;display:flex;gap:15px}
.social span{width:21px;height:21px;border-radius:50%;background:var(--white);display:block}
.foot-col{position:absolute;top:265px;font-size:17px;line-height:30px}
.foot-col h5{font-family:"Montserrat",Arial,sans-serif;font-size:17px;font-weight:600;margin-bottom:10px}
.foot-base{left:110px;top:520px;width:980px;height:1px;background:#3a3a3a}
.copyright{left:0;width:1200px;top:540px;text-align:center;font-size:17px}
</style>
</head>
<body>

<header class="site-header">
  <div class="abs brand"><div class="brand-mark"></div><div class="brand-name">MOSS QUAY</div></div>
  <nav class="abs nav"><span class="active">HOME</span><span>ABOUT</span><span>BLOG</span></nav>
  <svg class="abs search" width="26" height="26" viewBox="0 0 26 26" fill="none" stroke="#333" stroke-width="2"><circle cx="11" cy="11" r="8"/><path d="M17 17l7 7"/></svg>
  <div class="btn nav-cta">CONTACT US</div>
</header>

<section class="hero">
  <div class="abs head hero-kicker">Welcome <span>To</span></div>
  <h1 class="abs head hero-title"><b>Building</b> Businesses</h1>
  <div class="abs rule hero-rule"></div>
  <p class="abs hero-sub">Helping Content Creators Build Their Own Brand</p>
  <div class="btn hero-cta">GET STARTED</div>
  <div class="abs hero-art" role="img" aria-label="Illustration of a creator working on a laptop surrounded by content tools"></div>
</section>

<section class="about">
  <div class="abs about-art" role="img" aria-label="Illustration of digital marketing channels around the brand"></div>
  <h2 class="abs title about-head"><b>ABOUT</b> ME</h2>
  <div class="abs rule about-rule"></div>
  <p class="abs about-lead">Founded in 2024, we provide the highest level of goods and service.</p>
  <p class="abs about-text">Lorem ipsum dolor sit amet, consectetur adipiscing elit, sed do eiusmod tempor incididunt ut labore et dolore magna aliqua. Ut enim ad minim veniam, quis nostrud exercitation ullamco laboris nisi ut aliquip ex ea commodo consequat. Duis aute irure dolor in reprehenderit in voluptate velit esse cillum dolore eu fugiat nulla pariatur. Excepteur sint occaecat cupidatat non proident, sunt in culpa qui officia deserunt mollit anim id est laborum.</p>
  <div class="btn about-btn">Read More</div>
</section>

<section class="how">
  <h2 class="abs title how-head"><b>HOW ITS</b> WORKS</h2>
  <div class="abs rule how-rule"></div>
  <p class="abs how-text">Lorem ipsum dolor sit amet, consectetur adipiscing elit, sed do eiusmod tempor incididunt ut labore et dolore magna aliqua. Ut enim ad minim veniam, quis nostrud exercitation ullamco laboris nisi ut aliquip ex ea commodo consequat.</p>
  <div class="step" style="left:97px;width:317px">
    <div class="step-icon"><svg width="56" height="50" viewBox="0 0 56 50" fill="none" stroke="#fff" stroke-width="2.5"><rect x="3" y="3" width="50" height="34" rx="2"/><path d="M20 46h16M28 37v9M14 20l-5 4 5 4M42 20l5 4-5 4"/></svg></div>
    <h3>Lorem ipsum dolor</h3>
    <p>Engaging websites expertly crafted to convert your target audience.</p>
  </div>
  <div class="step featured" style="left:440px;width:320px">
    <div class="step-icon"><svg width="56" height="52" viewBox="0 0 56 52" fill="none" stroke="#445a63" stroke-width="2.5"><rect x="3" y="3" width="40" height="44" rx="2"/><circle cx="42" cy="34" r="10"/><path d="M39 29v10l8-5z"/></svg></div>
    <h3>Lorem ipsum dolor</h3>
    <p>Captivating video content that shares your brand's story and resonates with your audience.</p>
  </div>
  <div class="step" style="left:785px;width:317px">
    <div class="step-icon"><svg width="56" height="50" viewBox="0 0 56 50" fill="none" stroke="#fff" stroke-width="2.5"><rect x="3" y="3" width="50" height="34" rx="2"/><path d="M20 46h16M28 37v9M14 20l-5 4 5 4M42 20l5 4-5 4"/></svg></div>
    <h3>Custom Web Design</h3>
    <p>Engaging websites expertly crafted to convert your target audience.</p>
  </div>
</section>

<section class="why">
  <h2 class="abs title why-head"><b>WHY</b> CHOSSE US</h2>
  <div class="abs rule why-rule"></div>
  <p class="abs why-text">Lorem ipsum dolor sit amet, consectetur adipiscing elit, sed do eiusmod tempor incididunt ut labore et dolore magna aliqua.</p>

  <div class="reason" style="left:97px;top:192px"><div class="reason-icon"><svg width="52" height="52" viewBox="0 0 52 52" fill="none" stroke="#fff" stroke-width="2"><circle cx="26" cy="14" r="9"/><path d="M10 48V34M20 48V28M30 48V32M40 48V24"/></svg></div><div class="reason-body"><h4>Cultural Insights</h4><p>Crafting marketing messages that resonate deeply with regional audiences.</p></div></div>
  <div class="reason" style="left:612px;top:192px"><div class="reason-icon"><svg width="52" height="52" viewBox="0 0 52 52" fill="none" stroke="#fff" stroke-width="2"><circle cx="17" cy="34" r="9"/><circle cx="36" cy="38" r="6"/><path d="M32 6a8 8 0 0 1 5 14v4h-8v-4a8 8 0 0 1 3-14z"/></svg></div><div class="reason-body"><h4>Innovative Solutions</h4><p>Staying ahead with cutting-edge tools and technologies for brand growth.</p></div></div>
  <div class="reason" style="left:97px;top:315px"><div class="reason-icon"><svg width="52" height="52" viewBox="0 0 52 52" fill="none" stroke="#fff" stroke-width="2"><rect x="4" y="6" width="44" height="32"/><path d="M12 30l9-9 7 6 12-12M26 38v10M18 48h16"/></svg></div><div class="reason-body"><h4>Tailored Strategies</h4><p>Bespoke marketing approaches aligned with your business goals and target audience.</p></div></div>
  <div class="reason" style="left:612px;top:315px"><div class="reason-icon"><svg width="52" height="52" viewBox="0 0 52 52" fill="none" stroke="#fff" stroke-width="2"><circle cx="26" cy="12" r="6"/><path d="M16 30c0-6 20-6 20 0M6 22l8 20h8M46 22l-8 20h-8"/></svg></div><div class="reason-body"><h4>Dedicated Support</h4><p>Staying ahead with cutting-edge tools and technologies for brand growth.</p></div></div>
  <div class="reason" style="left:97px;top:438px"><div class="reason-icon"><svg width="52" height="52" viewBox="0 0 52 52" fill="none" stroke="#fff" stroke-width="2"><circle cx="26" cy="28" r="19"/><path d="M22 6h8M18 36V28M24 36V22M30 36V26M36 36V30"/></svg></div><div class="reason-body"><h4>Measurable Results</h4><p>Delivering quantifiable outcomes with detailed analytics to track your marketing success.</p></div></div>
  <div class="reason" style="left:612px;top:438px"><div class="reason-icon"><svg width="52" height="52" viewBox="0 0 52 52" fill="none" stroke="#fff" stroke-width="2"><path d="M26 4l14 6v10c0 8-6 14-14 18-8-4-14-10-14-18V10z"/><path d="M20 20l5 5 8-9M6 36l14 12M46 36L32 48"/></svg></div><div class="reason-body"><h4>Trusted Partnership</h4><p>Fostering lasting relationships as an extension of your team to achieve marketing objectives.</p></div></div>
</section>

<section class="blog">
  <h2 class="abs title blog-head"><b>LATEST</b> BLOG</h2>
  <div class="abs rule blog-rule"></div>
  <article class="post" style="left:110px">
    <div class="post-photo" role="img" aria-label="Photo of business people walking in a city" style="background:linear-gradient(180deg,#9fb0bb,#4c545c)"></div>
    <h3>Finibus Bonorum et Malorum</h3>
    <p>Nemo enim ipsam voluptatem quia voluptas sit aspernatur aut odit aut fugit.</p>
    <div class="more">READ MORE <svg width="16" height="12" viewBox="0 0 16 12" fill="none" stroke="#1d2529" stroke-width="1.8"><path d="M1 6h13M9 1l5 5-5 5"/></svg></div>
  </article>
  <article class="post" style="left:445px">
    <div class="post-photo" role="img" aria-label="Photo of a team typing at laptops in an office" style="background:linear-gradient(180deg,#e6e8ea,#b9bec2)"></div>
    <h3>Finibus Bonorum et Malorum</h3>
    <p>Nemo enim ipsam voluptatem quia voluptas sit aspernatur aut odit aut fugit.</p>
    <div class="more">READ MORE <svg width="16" height="12" viewBox="0 0 16 12" fill="none" stroke="#1d2529" stroke-width="1.8"><path d="M1 6h13M9 1l5 5-5 5"/></svg></div>
  </article>
  <article class="post" style="left:779px">
    <div class="post-photo" role="img" aria-label="Photo of colleagues reviewing work at a computer" style="background:linear-gradient(180deg,#8e9c8a,#c9c3b6)"></div>
    <h3>Finibus Bonorum et Malorum</h3>
    <p>Nemo enim ipsam voluptatem quia voluptas sit aspernatur aut odit aut fugit.</p>
    <div class="more">READ MORE <svg width="16" height="12" viewBox="0 0 16 12" fill="none" stroke="#1d2529" stroke-width="1.8"><path d="M1 6h13M9 1l5 5-5 5"/></svg></div>
  </article>
</section>

<section class="contact">
  <h2 class="abs title contact-head"><b>CONTACT</b> US</h2>
  <div class="field" style="left:182px;top:142px;width:410px;height:48px">Name</div>
  <div class="field" style="left:605px;top:142px;width:411px;height:48px">Email</div>
  <div class="field" style="left:182px;top:205px;width:410px;height:48px">Phone Number</div>
  <div class="field" style="left:605px;top:205px;width:411px;height:48px">Subject</div>
  <div class="field" style="left:182px;top:267px;width:834px;height:86px">Message</div>
  <div class="btn submit">Submit</div>
</section>

<footer class="site-footer">
  <div class="partner" style="left:110px"><div class="partner-mark"></div><div class="partner-bar"></div></div>
  <div class="partner" style="left:358px"><div class="partner-mark"></div><div class="partner-bar"></div></div>
  <div class="partner" style="left:632px"><div class="partner-mark"></div><div class="partner-bar"></div></div>
  <div class="partner" style="left:880px"><div class="partner-mark"></div><div class="partner-bar"></div></div>
  <div class="abs foot-rule"></div>

  <div class="abs foot-brand"><div class="foot-mark"></div><div class="foot-name">MOSS QUAY</div></div>
  <div class="abs foot-contact"><b>CALL:</b> 555-010-2040<br><b>MAIL:</b> hello@mossquay.io</div>
  <div class="abs social" aria-label="Social links"><span></span><span></span></div>

  <div class="foot-col" style="left:457px"><h5>QUICK LINKD</h5>Home<br>About Me<br>Blog<br>Contact Us</div>
  <div class="foot-col" style="left:685px"><h5>SUPPORT</h5>Help Center &amp; FAQs<br>Contact Us<br>Developer API Docs<br>Employer Resources<br>Account Login</div>
  <div class="foot-col" style="left:945px"><h5>LEGAL</h5>Terms of Service<br>Privacy Policy<br>FCRA Obligations</div>

  <div class="abs foot-base"></div>
  <p class="abs copyright">2024 Moss Quay. All Rights Reserved.</p>
</footer>

</body>
</html>
```